Specialised investor in e-mobility and energy wants business card design

We need a business card design that fits our existing corporate design. <The look and feel must be 'sharp'/'clean', dynamic, communicate momentum, professionalism etc (as one would imagine from a firm in the financial sector). We like the idea of a reverse-side of the card that includes the logo, and the name and contact details on the other. We expect the deliverable to be whatever format might be required to be able to get cards printed directly by a service such as kelmo press. Our website is www.zub.capital

```html
<!DOCTYPE html>
<html lang="en">
<head>
<meta charset="utf-8">
<title>ZUB Capital – Business Card</title>
<link rel="stylesheet" href="https://fonts.googleapis.com/css2?family=Montserrat:wght@400;500;700&display=swap">
<style>
  :root {
    --green-dark: #2f5128;
    --green-light: #7ab648;
    --ink: #2b2b2b;
    --paper: #ffffff;
    --backdrop: #e9ebe6;
    --rule: #9cc77a;
  }
  * { box-sizing: border-box; margin: 0; padding: 0; }
  html, body { width: 1200px; height: 960px; overflow: hidden; }
  body {
    background: var(--backdrop);
    font-family: 'Montserrat', sans-serif;
    position: relative;
  }
  .card {
    position: absolute;
    left: 240px;
    width: 720px;
    height: 411px;
    background: var(--paper);
    border-radius: 36px;
    overflow: hidden;
    box-shadow: 0 6px 18px rgba(0,0,0,0.12);
  }
  .card--front { top: 44px; }
  .card--back { top: 505px; }

  /* front */
  .front-brand {
    position: absolute;
    inset: 0;
    display: flex;
    align-items: center;
    justify-content: center;
    gap: 22px;
  }
  .brand-dot {
    width: 30px; height: 30px;
    border-radius: 50%;
    background: var(--green-dark);
  }
  .brand-name {
    color: var(--green-dark);
    font-weight: 500;
    letter-spacing: 1px;
  }
  .front-brand .brand-name { font-size: 84px; }

  /* back */
  .back-art { position: absolute; inset: 0; }
  .back-brand {
    position: absolute;
    left: 70px;
    top: 292px;
    display: flex;
    align-items: center;
    gap: 12px;
  }
  .back-brand .brand-dot { width: 16px; height: 16px; }
  .back-brand .brand-name { font-size: 40px; }

  .divider {
    position: absolute;
    left: 392px;
    top: 190px;
    width: 1px;
    height: 180px;
    background: var(--rule);
  }
  .details {
    position: absolute;
    left: 420px;
    top: 178px;
    color: var(--ink);
  }
  .person-name {
    color: var(--green-light);
    font-weight: 700;
    font-size: 25px;
    letter-spacing: 0.5px;
    text-transform: uppercase;
  }
  .person-title { font-size: 16px; margin-top: 2px; }
  .contact-list { list-style: none; margin-top: 14px; }
  .contact-list li {
    display: flex;
    align-items: center;
    gap: 8px;
    font-size: 15px;
    line-height: 23px;
  }
  .contact-list svg { width: 13px; height: 13px; fill: var(--green-dark); flex: none; }
  .company { margin-top: 14px; font-size: 16px; line-height: 22px; }
  .company-name { color: var(--green-light); }
</style>
</head>
<body>

  <section class="card card--front" aria-label="Card front">
    <div class="front-brand">
      <span class="brand-dot"></span>
      <span class="brand-name">ZUB Capital</span>
    </div>
  </section>

  <section class="card card--back" aria-label="Card back">
    <svg class="back-art" viewBox="0 0 720 411" width="720" height="411" aria-hidden="true">
      <path d="M0,0 H720 V72 C560,88 300,160 0,262 Z" fill="var(--green-dark)"/>
      <path d="M0,278 C300,176 540,104 720,86" fill="none" stroke="var(--green-light)" stroke-width="9"/>
    </svg>

    <div class="back-brand">
      <span class="brand-dot"></span>
      <span class="brand-name">ZUB Capital</span>
    </div>

    <div class="divider"></div>

    <div class="details">
      <p class="person-name">Marek Olsson</p>
      <p class="person-title">Managing Director</p>
      <ul class="contact-list">
        <li>
          <svg viewBox="0 0 16 16"><path d="M3 1h3l1.5 4-2 1.5a9 9 0 0 0 4 4L11 8.5l4 1.5v3a2 2 0 0 1-2 2A13 13 0 0 1 1 3a2 2 0 0 1 2-2z"/></svg>
          +41 79 555 0142
        </li>
        <li>
          <svg viewBox="0 0 16 16"><path d="M1 3h14v10H1z M1 3l7 6 7-6" stroke="#fff" stroke-width="1.2"/></svg>
          marek@zub.capital
        </li>
        <li>
          <svg viewBox="0 0 16 16"><circle cx="8" cy="8" r="7"/></svg>
          www.zub.capital
        </li>
      </ul>
      <div class="company">
        <p class="company-name">ZUB Capital S.A.</p>
        <p>Geneva, Switzerland</p>
      </div>
    </div>
  </section>

</body>
</html>
```